Email Marketing Campaign 50% discount and buy-2-get-1 offer

I would like to inform my customers of our special offers via a e-Newsletter/Marketing E-Mail.

The coding needs to be done by the designer.

I have most of the design and the message that we wish to convey our buyers.

The information is:

1. We have now 50% discount on all our carpets

2. We have a buy-2 get-1 free carpet offer

For both the above messages we have already banner style that we like to use in our Newsletter.
I have attached the banner and the designers can use it.

3. We have opened a new shop in Berlin Germany

Therefore we like to have a Sylish Newsletter design that fits our website and products using the banner idea and we wish to include the 3 messages.
Special note should be given that this newsletter is going to our previous buyers. Therefore they already know us, and we just like to inform them of our latest news and offer.

Target Market(s)

Upmarket buyers looking for a great deal

Industry/Entity Type

Marketing

Coding

Coded - Design and coding required

Number of Pages Required

1 page

Font styles to use
Sans Serif

Colors
e667a6
34a7d8

Requirements
Must have
• Clear explanation with excitement in the message
Nice to have
• To promote clearly the 3 for 2 with maybe an explanation and clear images describing what the promotion is and how it works.
• I.e. buy 2 get 1 extra carpet of your choice free
• Add carpets to checkout and the system will calculate automatically
• The lowest carpet in your selection of 3 is the free carpet

```html
<!DOCTYPE html>
<html lang="en">
<head>
<meta charset="utf-8">
<title>Carpet Offers Newsletter Banner</title>
<link rel="stylesheet" href="https://fonts.googleapis.com/css2?family=Lato:wght@400;700;900&display=swap">
<style>
  :root {
    --pink: #e6077a;
    --blue: #1b8ee0;
    --red: #cc1f2c;
    --red-dark: #a8141f;
    --red-ring: #e0333f;
    --yellow: #ffec00;
    --ink: #111111;
    --panel-dark: rgba(10, 10, 10, 0.88);
    --white: #ffffff;
    --btn-text: #333333;
  }
  * { margin: 0; padding: 0; box-sizing: border-box; }
  html, body { width: 1200px; height: 624px; overflow: hidden; }
  body { font-family: "Lato", Arial, sans-serif; }

  .banner { position: relative; width: 1200px; height: 624px; overflow: hidden; }

  .room-photo {
    position: absolute; inset: 0;
    background:
      linear-gradient(180deg, rgba(0,0,0,0) 55%, rgba(40,28,30,0.75) 100%),
      radial-gradient(ellipse at 45% 20%, #9fc25a 0%, rgba(159,194,90,0) 14%),
      linear-gradient(90deg, #8c7f72 0%, #b3a697 30%, #a49583 55%, #8f7d6a 75%, #cfc6bb 100%);
  }

  .offer-card { position: absolute; top: 156px; width: 285px; height: 392px; }
  .sale-card { left: 106px; background: var(--panel-dark); border-top: 7px solid var(--pink); color: var(--white); }
  .store-card { left: 770px; background: var(--blue); border-top: 5px solid var(--white); }

  .sale-card span { position: absolute; font-weight: 900; line-height: 1; white-space: nowrap; }
  .sale-upto { left: 40px; top: 36px; font-size: 27px; }
  .sale-fifty { left: 30px; top: 55px; font-size: 92px; letter-spacing: -3px; }
  .sale-off { right: 55px; top: 131px; font-size: 34px; }
  .sale-word { left: 34px; top: 149px; font-size: 100px; letter-spacing: -2px; }
  .sale-now { right: 29px; top: 252px; font-size: 28px; }
  .sale-extra {
    position: absolute; left: 24px; right: 24px; top: 292px;
    font-size: 13.5px; font-weight: 400; line-height: 1.2; text-align: center;
  }

  .shop-button {
    position: absolute; top: 530px; width: 142px; height: 29px;
    background: var(--white); border-radius: 2px;
    font-size: 11px; line-height: 29px; text-align: center; color: var(--btn-text);
    text-decoration: none; box-shadow: 0 1px 3px rgba(0,0,0,0.25);
  }
  .shop-button--sale { left: 178px; color: var(--pink); }
  .shop-button--bundle { left: 510px; }
  .shop-button--store { left: 841px; color: var(--blue); }

  .bundle-badge { position: absolute; left: 460px; top: 138px; width: 242px; height: 392px; }
  .bundle-badge svg { position: absolute; inset: 0; }
  .bundle-code {
    position: absolute; left: 0; width: 242px; top: 61px; text-align: center;
    font-size: 100px; font-weight: 900; color: var(--white); line-height: 88px; letter-spacing: -1px;
  }
  .bundle-copy {
    position: absolute; left: 0; width: 242px; top: 256px; text-align: center;
    color: var(--white); font-weight: 900; line-height: 1;
  }
  .bundle-copy .line-md { display: block; font-size: 25px; }
  .bundle-copy .line-sm { display: block; font-size: 10px; letter-spacing: 3px; color: var(--yellow); margin: 0; }
  .bundle-copy .line-lg { display: block; font-size: 42px; margin-top: 1px; }

  .store-icon { position: absolute; left: 66px; top: 31px; width: 154px; height: 162px; }
  .store-burst { position: absolute; left: 112px; top: 149px; width: 192px; height: 192px; }
  .store-burst svg { position: absolute; inset: 0; }
  .burst-text { position: absolute; inset: 0; display: flex; flex-direction: column; align-items: center; justify-content: center; font-weight: 900; line-height: 0.9; white-space: nowrap; }
  .burst-small { color: var(--yellow); font-size: 15px; margin-bottom: 3px; }
  .burst-big { color: var(--white); font-size: 50px; }
  .burst-city { color: var(--yellow); font-size: 15px; margin-top: 4px; }
</style>
</head>
<body>
<main class="banner">
  <div class="room-photo" role="img" aria-label="Photo of a bright living room with sofa, window to green trees, fireplace and a patterned rug"></div>

  <section class="offer-card sale-card">
    <span class="sale-upto">up to</span>
    <span class="sale-fifty">50%</span>
    <span class="sale-off">OFF</span>
    <span class="sale-word">sale</span>
    <span class="sale-now">now on!</span>
    <p class="sale-extra">BUY ONE CARPET GET EXTRA 50% OFF</p>
  </section>
  <a class="shop-button shop-button--sale" href="#">Shop Now</a>

  <section class="bundle-badge">
    <svg viewBox="0 0 242 392" aria-hidden="true">
      <polygon points="23,182 218,182 218,390 120,362 23,390" fill="var(--ink)"/>
      <circle cx="121" cy="120" r="117" fill="var(--red-ring)"/>
      <circle cx="121" cy="120" r="100" fill="var(--red-dark)"/>
      <circle cx="121" cy="120" r="94" fill="var(--red)"/>
    </svg>
    <div class="bundle-code">B2<br>GO</div>
    <p class="bundle-copy">
      <span class="line-md">BUY TWO</span>
      <span class="line-sm">CARPETS</span>
      <span class="line-md">GET ONE</span>
      <span class="line-lg">FREE</span>
    </p>
  </section>
  <a class="shop-button shop-button--bundle" href="#">Shop Now</a>

  <section class="offer-card store-card">
    <svg class="store-icon" viewBox="0 0 160 168" aria-hidden="true" fill="none" stroke="var(--white)" stroke-width="7">
      <rect x="6" y="4" width="148" height="10" fill="var(--white)" stroke="none"/>
      <path d="M6 14 H154 V40 H6 Z"/>
      <path d="M24 14 V40 M42 14 V40 M60 14 V40 M80 14 V40 M100 14 V40 M118 14 V40 M136 14 V40"/>
      <path d="M14 44 V164 H146 V44"/>
      <rect x="28" y="64" width="68" height="86"/>
      <path d="M40 96 L58 78 M44 108 L68 84" stroke-width="5"/>
      <rect x="108" y="64" width="30" height="100"/>
      <circle cx="116" cy="114" r="3" fill="var(--white)" stroke="none"/>
    </svg>
    <div class="store-burst">
      <svg viewBox="-100 -100 200 200" aria-hidden="true">
        <polygon fill="var(--red)" points="96,0 79.2,21.2 83.1,48 58,58 48,83.1 21.2,79.2 0,96 -21.2,79.2 -48,83.1 -58,58 -83.1,48 -79.2,21.2 -96,0 -79.2,-21.2 -83.1,-48 -58,-58 -48,-83.1 -21.2,-79.2 0,-96 21.2,-79.2 48,-83.1 58,-58 83.1,-48 79.2,-21.2"/>
      </svg>
      <div class="burst-text">
        <span class="burst-small">NEW STORE</span>
        <span class="burst-big">NEW</span>
        <span class="burst-big">OPEN</span>
        <span class="burst-city">BERLIN, GERMANY</span>
      </div>
    </div>
  </section>
  <a class="shop-button shop-button--store" href="#">Shop Now</a>
</main>
</body>
</html>
```